Satchel & Sundial needs new business card design

I need a new business card design. I'm looking for out-of-the-box design which represents the freedom of being a location independent entrepreneur.
I offer coaching, retreats and trips.
I would like to see designs with and without the photo.
Colors I use are black (#000000), green (#25A796) and brown (#D7C38C)
Website satchelandsundial.example

Target Market(s)

location independent entrepreneurs, digital nomads, people looking to swap the 9 to 5 for a lifestyle business

Industry/Entity Type

Business

Contact Information for Business Card

Dorota Falkner
Your Lifestyle Business Coach, Retreat & Trip Leader
http://satchelandsundial.example
hello@satchelandsundial.example
Live a life you don't need a holiday from

Font styles to use
Serif
Sans Serif

Requirements
Must have
• One side should contain only the logo. I would also consider having the "Live a life you don't need a holiday from" on that side too (depending on how it looks)
• Please show both sides on the designs.

```html
<!DOCTYPE html>
<html lang="en">
<head>
<meta charset="utf-8">
<title>Satchel &amp; Sundial — Business Card</title>
<link rel="stylesheet" href="https://fonts.googleapis.com/css2?family=Open+Sans:ital,wght@0,400;0,600;0,700;1,400&display=swap">
<style>
  :root {
    --page-bg: #ececec;
    --card-bg: #ffffff;
    --ink: #1f1d1e;
    --teal: #25a796;
    --muted: #555555;
    --pattern-tone: #f1f1f1;
  }
  * { box-sizing: border-box; margin: 0; padding: 0; }
  html, body {
    width: 1105px;
    height: 1200px;
    overflow: hidden;
    background: var(--page-bg);
    font-family: "Open Sans", Arial, sans-serif;
  }
  .canvas {
    position: relative;
    width: 1105px;
    height: 1200px;
  }
  .card {
    position: absolute;
    left: 192px;
    width: 721px;
    height: 411px;
    background: var(--card-bg);
    overflow: hidden;
  }
  .card--front { top: 146px; }
  .card--back  { top: 602px; }

  .corner-shapes {
    position: absolute;
    inset: 0;
    width: 100%;
    height: 100%;
  }

  .brand-name {
    position: absolute;
    font-weight: 600;
    color: var(--ink);
    white-space: nowrap;
    letter-spacing: 0.01em;
  }
  .card--front .brand-name {
    right: 44px;
    top: 62px;
    font-size: 44px;
  }

  .contact-block {
    position: absolute;
    left: 41px;
    top: 222px;
  }
  .person-name {
    font-size: 25px;
    font-weight: 700;
    color: var(--teal);
    text-transform: uppercase;
    letter-spacing: 0.02em;
    line-height: 1.2;
  }
  .person-role {
    font-size: 19px;
    color: var(--ink);
    line-height: 1.4;
  }
  .contact-list {
    list-style: none;
    margin-top: 14px;
  }
  .contact-item {
    display: flex;
    align-items: center;
    gap: 10px;
    font-size: 18px;
    color: var(--muted);
    line-height: 1.55;
  }
  .contact-icon { width: 18px; height: 18px; flex: none; }

  .pattern-field {
    position: absolute;
    inset: 0;
    background: linear-gradient(160deg, var(--pattern-tone), #fafafa 55%, var(--pattern-tone));
  }
  .social-squares {
    position: absolute;
    top: 26px;
    right: 20px;
    display: flex;
    gap: 5px;
  }
  .social-square {
    width: 25px;
    height: 25px;
    background: var(--teal);
  }
  .card--back .brand-name {
    left: 0;
    right: 0;
    top: 160px;
    text-align: center;
    font-size: 64px;
  }
  .tagline {
    position: absolute;
    left: 0;
    right: 0;
    top: 350px;
    text-align: center;
    font-size: 18px;
    font-style: italic;
    color: var(--ink);
  }
</style>
</head>
<body>
<main class="canvas">

  <section class="card card--front" aria-label="Card front">
    <svg class="corner-shapes" viewBox="0 0 721 411" preserveAspectRatio="none" aria-hidden="true">
      <polygon points="0,0 232,0 0,189" fill="var(--ink)"/>
      <polygon points="611,411 721,323 721,411" fill="var(--teal)"/>
    </svg>

    <div class="brand-name">Satchel &amp; Sundial</div>

    <div class="contact-block">
      <h1 class="person-name">Dorota Falkner</h1>
      <p class="person-role">Your Lifestyle Business Coach</p>
      <p class="person-role">Retreat &amp; Trip Leader</p>
      <ul class="contact-list">
        <li class="contact-item">
          <svg class="contact-icon" viewBox="0 0 18 18" aria-hidden="true">
            <rect x="1" y="4" width="16" height="11" rx="1" fill="var(--teal)"/>
            <polyline points="1.5,4.8 9,10.5 16.5,4.8" fill="none" stroke="#fff" stroke-width="1.4"/>
          </svg>
          hello@satchelandsundial.example
        </li>
        <li class="contact-item">
          <svg class="contact-icon" viewBox="0 0 18 18" aria-hidden="true">
            <circle cx="9" cy="9" r="8" fill="var(--teal)"/>
            <ellipse cx="9" cy="9" rx="3.5" ry="8" fill="none" stroke="#fff" stroke-width="1.2"/>
            <line x1="1" y1="9" x2="17" y2="9" stroke="#fff" stroke-width="1.2"/>
          </svg>
          www.satchelandsundial.example
        </li>
      </ul>
    </div>
  </section>

  <section class="card card--back" aria-label="Card back">
    <div class="pattern-field" role="img" aria-label="Faint repeating pattern of the brand name across the card"></div>

    <div class="social-squares" aria-label="Social profiles">
      <span class="social-square"></span>
      <span class="social-square"></span>
      <span class="social-square"></span>
    </div>

    <div class="brand-name">Satchel &amp; Sundial</div>

    <p class="tagline">Live a life you don't need a holiday from</p>
  </section>

</main>
</body>
</html>
```